need a clean, modern job advertisement designed for social media (Facebook & Instagram).

The post is to advertise two positions:
• Leading Hand Boilermaker
• Dragline Fitter
We want the design to match our KPR Site Services branding: blue, white, strong, professional, mining-industry style.
What the design should include:
Bold headline: “WE’RE HIRING”
Sub-headline: “Leading Hand Boilermaker & Dragline Fitter”
Key points:
• Tallon Basin based
• Dragline & shovel maintenance
• Great pay + long-term work
• Locally owned & operated
KPR logo placed cleanly
Space for 1–2 images (boilermaking or dragline work)
Design style:
Strong and industrial
Blue/white colour scheme
Easy to read at a glance
Suitable for a square 1080×1080 design

```html
<!DOCTYPE html>
<html lang="en">
<head>
<meta charset="utf-8">
<title>KPR Site Services – We're Hiring</title>
<link rel="stylesheet" href="https://fonts.googleapis.com/css2?family=Oswald:wght@300;400;500&family=Roboto+Condensed:wght@300;400&family=Open+Sans:ital,wght@0,700;1,700&display=swap">
<style>
  :root {
    --bg: #151515;
    --bg-deep: #0b0b0b;
    --grey-dark: #8f9294;
    --grey-light: #e2e3e4;
    --blue: #1ba3e1;
    --blue-soft: #5cb8ea;
    --white: #ffffff;
    --text-soft: #d9d9d9;
    --headline-grey: #6c6e70;
    --yellow: #f6b81c;
    --ink: #161616;
  }
  * { margin: 0; padding: 0; box-sizing: border-box; }
  html, body { width: 1200px; height: 1200px; overflow: hidden; background: var(--bg); }
  .poster {
    position: relative;
    width: 1200px;
    height: 1200px;
    overflow: hidden;
    background: var(--bg);
    font-family: "Roboto Condensed", sans-serif;
    color: var(--white);
  }
  .backdrop { position: absolute; inset: 0; width: 1200px; height: 1200px; }

  .brand {
    position: absolute;
    left: 70px;
    top: 190px;
    width: 390px;
    display: flex;
    align-items: center;
    gap: 16px;
    font-family: "Oswald", sans-serif;
    font-weight: 500;
    font-size: 44px;
    line-height: 1.05;
    text-transform: uppercase;
    color: var(--ink);
  }
  .brand-mark {
    flex: 0 0 auto;
    width: 58px;
    height: 58px;
    border-radius: 50%;
    background: var(--blue);
  }

  .headline {
    position: absolute;
    right: 56px;
    display: block;
    font-family: "Oswald", sans-serif;
    font-weight: 400;
    line-height: 1;
    text-align: right;
    white-space: nowrap;
    transform-origin: right top;
  }
  .headline-were {
    top: 209px;
    font-size: 206px;
    letter-spacing: -1px;
    color: var(--headline-grey);
    transform: scaleX(0.88);
  }
  .headline-hiring {
    top: 395px;
    font-size: 275px;
    letter-spacing: -2px;
    color: var(--blue);
    transform: scaleX(0.85);
  }

  .join-badge { position: absolute; left: 278px; top: 478px; width: 260px; height: 180px; }
  .join-icon {
    position: absolute; left: 0; top: 10px;
    width: 110px; height: 150px;
    border-radius: 14px;
    background: linear-gradient(160deg, var(--yellow), #e39a10);
  }
  .join-label {
    position: absolute;
    font-family: "Open Sans", sans-serif;
    font-weight: 700;
    line-height: 1;
  }
  .join-label-top {
    left: 122px; top: 66px; padding: 5px 14px;
    background: var(--yellow); color: var(--ink); font-size: 34px;
  }
  .join-label-bottom {
    left: 89px; top: 110px; padding: 8px 14px;
    background: var(--blue); color: var(--white); font-size: 48px;
  }

  .subheadline {
    position: absolute;
    left: 0; right: 66px; top: 686px;
    text-align: right;
    font-family: "Open Sans", sans-serif;
    font-weight: 700;
    font-size: 40px;
    letter-spacing: 1.5px;
    white-space: nowrap;
    color: var(--white);
  }

  .work-photo {
    position: absolute;
    top: 774px;
    height: 313px;
  }
  .work-photo-welding { left: 50px; width: 297px; background: linear-gradient(160deg, #3b3330, #17120f 60%, #5a3a22); }
  .work-photo-vehicle { left: 370px; width: 294px; background: linear-gradient(180deg, #c9a27a, #4b5548 45%, #d8dadc 70%, #3b3d3f); }

  .why-us { position: absolute; left: 703px; top: 834px; }
  .why-us-title {
    font-family: "Open Sans", sans-serif;
    font-weight: 700;
    font-size: 36px;
    line-height: 1;
    margin-bottom: 22px;
  }
  .why-us-list { list-style: none; }
  .why-us-list li {
    font-size: 32px;
    font-weight: 300;
    line-height: 51px;
    color: var(--text-soft);
    white-space: nowrap;
  }
  .why-us-list li::before { content: "• "; }

  .web-address {
    position: absolute;
    left: 476px; top: 1123px;
    font-family: "Open Sans", sans-serif;
    font-weight: 700;
    font-style: italic;
    font-size: 50px;
    letter-spacing: 2px;
    line-height: 1;
    white-space: nowrap;
    color: var(--white);
  }
</style>
</head>
<body>
<main class="poster">
  <svg class="backdrop" viewBox="0 0 1080 1080" aria-hidden="true">
    <defs>
      <linearGradient id="panel-grey" x1="0" y1="0" x2="1" y2="0.3">
        <stop offset="0" stop-color="#8f9294"/>
        <stop offset="0.6" stop-color="#d4d5d6"/>
        <stop offset="1" stop-color="#e9eaeb"/>
      </linearGradient>
      <linearGradient id="band-silver" x1="0" y1="1" x2="1" y2="0">
        <stop offset="0" stop-color="#f2f2f2"/>
        <stop offset="1" stop-color="#7d8082"/>
      </linearGradient>
      <linearGradient id="arrow-blue" x1="0" y1="0" x2="1" y2="0">
        <stop offset="0" stop-color="#ffffff"/>
        <stop offset="1" stop-color="#1ba3e1"/>
      </linearGradient>
      <radialGradient id="bg-glow" cx="0.7" cy="0.45" r="0.6">
        <stop offset="0" stop-color="#262626"/>
        <stop offset="1" stop-color="#121212"/>
      </radialGradient>
    </defs>
    <rect width="1080" height="1080" fill="url(#bg-glow)"/>
    <polygon points="0,0 790,0 0,640" fill="url(#panel-grey)"/>
    <polygon points="790,0 855,0 0,700 0,640" fill="#0d0d0d"/>
    <polygon points="855,0 885,0 0,728 0,700" fill="url(#band-silver)"/>
    <polygon points="885,0 895,0 0,737 0,728" fill="#3aa6e3"/>
    <polygon points="0,330 150,470 0,610" fill="#0b0b0b"/>
    <polygon points="18,415 110,490 18,565" fill="url(#arrow-blue)"/>
    <rect x="615" y="703" width="465" height="3" fill="#8fb8d2"/>
    <rect x="0" y="1038" width="400" height="3" fill="#4f9fcf"/>
  </svg>

  <div class="brand">
    <span class="brand-mark"></span>
    <span class="brand-name">KPR Site Services</span>
  </div>

  <h1>
    <span class="headline headline-were">WE’RE</span>
    <span class="headline headline-hiring">HIRING</span>
  </h1>

  <div class="join-badge">
    <div class="join-icon" role="img" aria-label="Megaphone illustration"></div>
    <span class="join-label join-label-top">JOIN</span>
    <span class="join-label join-label-bottom">NOW</span>
  </div>

  <h2 class="subheadline">Leading Hand Boilermaker &amp; Dragline Fitter</h2>

  <div class="work-photo work-photo-welding" role="img" aria-label="Photo of a boilermaker welding beneath heavy mining equipment"></div>
  <div class="work-photo work-photo-vehicle" role="img" aria-label="Photo of a company service ute parked on site at sunset"></div>

  <section class="why-us">
    <h3 class="why-us-title">WHY US</h3>
    <ul class="why-us-list">
      <li>Tallon Basin based</li>
      <li>Dragline &amp; shovel maintenance</li>
      <li>Great pay + long-term work</li>
      <li>Locally owned &amp; operated</li>
    </ul>
  </section>

  <p class="web-address">www.kprsiteservices.com</p>
</main>
</body>
</html>
```